Business Card Design needed - Something Awesome!

Need a business card designed. Company is "Marlowe Advisory" we do consulting and also have sales automation technology.
I'm going to use thick stock or metal, something really nice... I was thinking about a QR Code on the back that would just upload my contact info to the persons contact, etc -

This is a Strategy Company with a tech feel. I'm open to ideas but really want this to be nice!

I need a template that should include:

Name | Position or Title
D: 415.902.3376
www.marloweadvisory.example

I'm going to attach my contact so you can use that one, I need to get this printed.

Target Market(s)

Small to mid size customers, Entrepreneurs etc.

Industry/Entity Type

Consulting, Tech, Private Equity.

Contact Information for Business Card

Name, Phone, Maybe email, URL

Font styles to use
Sans Serif

Colors

Designer to choose only greyscale colors for use in the design.

Requirements
Must have
• Fresh, Clean, stand out from the crowd - will be on thick stock or metal.
Nice to have
• Clean, simple yet impactful.
Should not have
• Not cartoonish

```html
<!DOCTYPE html>
<html lang="en">
<head>
<meta charset="UTF-8">
<title>Marlowe Advisory – Business Card</title>
<link rel="stylesheet" href="https://fonts.googleapis.com/css2?family=Jost:wght@500&family=Poppins:wght@400;600&display=swap">
<style>
  :root {
    --page-bg: #e9e9eb;
    --frost-light: #f6f2f2;
    --frost-mid: #e4dcdc;
    --ink: #0a0a0a;
    --panel: #000000;
    --on-panel: #ffffff;
    --sheen-light: #ffffff;
    --sheen-dark: #8c8c8c;
  }
  html, body {
    margin: 0;
    width: 1200px;
    height: 900px;
    overflow: hidden;
    background: var(--page-bg);
  }
  .card {
    position: absolute;
    left: 100px;
    top: 141px;
    width: 1000px;
    height: 617px;
    overflow: hidden;
    box-shadow: 0 18px 40px rgba(0,0,0,0.18);
  }
  .card-shapes {
    position: absolute;
    inset: 0;
    width: 100%;
    height: 100%;
  }
  .brand-name {
    position: absolute;
    left: 65px;
    top: 150px;
    margin: 0;
    font-family: "Jost", sans-serif;
    font-weight: 500;
    font-size: 78px;
    line-height: 1;
    letter-spacing: 2px;
    color: var(--ink);
  }
  .holder {
    position: absolute;
    left: 513px;
    top: 240px;
    color: var(--on-panel);
  }
  .holder-name {
    margin: 0;
    font-family: "Poppins", sans-serif;
    font-weight: 600;
    font-size: 40px;
    line-height: 1.1;
    letter-spacing: 0.5px;
  }
  .holder-title {
    margin: 0;
    font-family: "Poppins", sans-serif;
    font-weight: 400;
    font-size: 28px;
    line-height: 1.2;
  }
  .contact-list {
    position: absolute;
    left: 482px;
    top: 370px;
    margin: 0;
    padding: 0;
    list-style: none;
    color: var(--on-panel);
    font-family: "Poppins", sans-serif;
    font-weight: 400;
    font-size: 28px;
    line-height: 36px;
  }
  .contact-item {
    display: flex;
    align-items: center;
    gap: 10px;
  }
  .contact-icon {
    width: 25px;
    height: 25px;
    flex: none;
  }
</style>
</head>
<body>
  <article class="card">
    <svg class="card-shapes" viewBox="0 0 1000 617" aria-hidden="true">
      <defs>
        <linearGradient id="frost" x1="0" y1="0" x2="1" y2="1">
          <stop offset="0" stop-color="var(--frost-light)"/>
          <stop offset="1" stop-color="var(--frost-mid)"/>
        </linearGradient>
        <linearGradient id="sheen" x1="0" y1="0" x2="0" y2="1">
          <stop offset="0" stop-color="var(--sheen-light)"/>
          <stop offset="0.6" stop-color="var(--sheen-dark)"/>
          <stop offset="1" stop-color="var(--sheen-dark)" stop-opacity="0"/>
        </linearGradient>
      </defs>
      <rect class="frost-face" width="1000" height="617" fill="url(#frost)"/>
      <path class="wave-sheen" fill="url(#sheen)"
        d="M439 0 L481 0 C515 40 515 150 480 260 C470 290 462 310 452 340 C485 230 492 120 439 0 Z"/>
      <path class="wave-panel" fill="var(--panel)"
        d="M481 0 C515 40 515 150 480 260 C450 350 410 430 425 520 C432 570 445 600 460 617 L1000 617 L1000 0 Z"/>
    </svg>

    <h1 class="brand-name">MARLOWE</h1>

    <div class="holder">
      <h2 class="holder-name">ELENA VARGA</h2>
      <p class="holder-title">Managing Director</p>
    </div>

    <ul class="contact-list">
      <li class="contact-item">
        <svg class="contact-icon" viewBox="0 0 24 24" aria-hidden="true">
          <path fill="#fff" d="M6.6 10.8a15.2 15.2 0 0 0 6.6 6.6l2.2-2.2a1 1 0 0 1 1-.25 11.4 11.4 0 0 0 3.6.57 1 1 0 0 1 1 1V20a1 1 0 0 1-1 1A17 17 0 0 1 3 4a1 1 0 0 1 1-1h3.5a1 1 0 0 1 1 1c0 1.25.2 2.45.57 3.57a1 1 0 0 1-.25 1z"/>
          <path fill="none" stroke="#fff" stroke-width="1.6" d="M14 3.5a7 7 0 0 1 6.5 6.5M14 7a3.5 3.5 0 0 1 3 3"/>
        </svg>
        <span>415.902.3376</span>
      </li>
      <li class="contact-item">
        <svg class="contact-icon" viewBox="0 0 24 24" aria-hidden="true">
          <rect x="2" y="5" width="20" height="14" fill="#fff"/>
          <path d="M2 5l10 8 10-8M2 19l7-6.5M22 19l-7-6.5" fill="none" stroke="#000" stroke-width="1.4"/>
        </svg>
        <span>info@marloweadvisory.example</span>
      </li>
      <li class="contact-item">
        <svg class="contact-icon" viewBox="0 0 24 24" aria-hidden="true">
          <g fill="none" stroke="#fff" stroke-width="1.8">
            <circle cx="12" cy="12" r="10"/>
            <ellipse cx="12" cy="12" rx="4.2" ry="10"/>
            <path d="M2 12h20M4 7h16M4 17h16"/>
          </g>
        </svg>
        <span>www.marloweadvisory.example</span>
      </li>
    </ul>
  </article>
</body>
</html>
```